Private Investigation Business Card Design

I need a business card for a new private investigation company named Brisk Inquiries. I perform mainly surveillance jobs, vehicle repossessions, document serves etc. The final design should aim for a professional look. The logo has a magnifying glass with stick man arms and legs and is in a running action to show the "Brisk" aspect of the name. If the colour scheme could remain the same as the website www.briskinquiries-demo.com.au with silvers,blacks and a couple electric blue highlights.
Industry/Entity Type
Business
Contact Information for Business Card
Morgan Kellaway
Brisk Inquiries
0487316204
PO Box 58, Carnwell NSW 2291
info@briskinquiries-demo.com.au
www.briskinquiries-demo.com.au
Look and feel

```html
<!DOCTYPE html>
<html lang="en">
<head>
<meta charset="utf-8">
<title>Brisk Inquiries – Business Card</title>
<link rel="stylesheet" href="https://fonts.googleapis.com/css2?family=Lato:wght@400;700;900&display=swap">
<style>
  :root {
    --backdrop: #e4e4e4;
    --card-front: #ffffff;
    --card-back: #3b3c3f;
    --ink-dark: #3d3d3d;
    --ink-mid: #555555;
    --rule: #6a6a6a;
    --mark-light: #8a8b8e;
    --mark-back: #9c9da1;
  }
  html, body {
    margin: 0;
    padding: 0;
    width: 1200px;
    height: 720px;
    overflow: hidden;
    background: var(--backdrop);
    font-family: "Lato", Arial, sans-serif;
  }
  .canvas {
    position: relative;
    width: 1200px;
    height: 720px;
  }
  .card {
    position: absolute;
    top: 241px;
    width: 419px;
    height: 239px;
    border-radius: 7px;
    box-sizing: border-box;
  }
  .card--front {
    left: 148px;
    background: var(--card-front);
    color: var(--ink-dark);
  }
  .card--back {
    left: 633px;
    background: var(--card-back);
  }
  .brand {
    position: absolute;
    display: flex;
    align-items: center;
    gap: 10px;
    font-weight: 900;
    white-space: nowrap;
  }
  .brand__dot {
    border-radius: 50%;
    flex: none;
  }
  .card--front .brand {
    left: 20px;
    top: 20px;
    font-size: 24px;
    color: var(--mark-light);
  }
  .card--front .brand__dot {
    width: 18px;
    height: 18px;
    background: var(--mark-light);
  }
  .card--back .brand {
    left: 0;
    right: 0;
    top: 98px;
    justify-content: center;
    font-size: 36px;
    color: var(--mark-back);
  }
  .card--back .brand__dot {
    width: 24px;
    height: 24px;
    background: var(--mark-back);
  }
  .person {
    position: absolute;
    left: 20px;
    top: 108px;
    right: 20px;
  }
  .person__name {
    margin: 0;
    font-size: 18px;
    font-weight: 700;
    color: var(--ink-dark);
    line-height: 1.1;
  }
  .person__role {
    display: flex;
    align-items: flex-end;
    gap: 3px;
    margin-top: 3px;
    font-size: 13px;
    color: var(--ink-mid);
  }
  .person__rule {
    flex: 1;
    height: 1px;
    background: var(--rule);
    margin-bottom: 3px;
  }
  .contact {
    position: absolute;
    left: 20px;
    bottom: 17px;
    margin: 0;
    padding: 0;
    list-style: none;
    font-size: 12px;
    line-height: 13px;
    color: var(--ink-dark);
  }
  .contact__item {
    display: flex;
    align-items: center;
    gap: 5px;
  }
  .contact__icon {
    width: 11px;
    height: 10px;
    fill: none;
    stroke: var(--ink-dark);
    stroke-width: 1.4;
  }
  .address {
    position: absolute;
    right: 20px;
    bottom: 17px;
    margin: 0;
    font-style: normal;
    text-align: right;
    font-size: 12px;
    line-height: 13px;
    color: var(--ink-dark);
  }
</style>
</head>
<body>
<main class="canvas">
  <section class="card card--front" aria-label="Business card front">
    <div class="brand">
      <span>Brisk Inquiries</span>
      <span class="brand__dot"></span>
    </div>
    <div class="person">
      <h1 class="person__name">Morgan Kellaway</h1>
      <div class="person__role"><span>Director</span><span class="person__rule"></span></div>
    </div>
    <ul class="contact">
      <li class="contact__item">
        <svg class="contact__icon" viewBox="0 0 11 10" aria-hidden="true"><path d="M1 3 Q5.5 0 10 3 L9 4.5 L7.5 4 M1 3 L2 4.5 L3.5 4 M3 5 H8 L9 9 H2 Z" fill="var(--ink-dark)" stroke-width="0.8"/></svg>
        <span>0487316204</span>
      </li>
      <li class="contact__item">
        <svg class="contact__icon" viewBox="0 0 11 10" aria-hidden="true"><rect x="0.5" y="1.5" width="10" height="7" fill="var(--ink-dark)" stroke="none"/><path d="M0.8 2 L5.5 5.8 L10.2 2" stroke="#fff" stroke-width="1"/></svg>
        <span>info@briskinquiries-demo.com.au</span>
      </li>
      <li class="contact__item">
        <svg class="contact__icon" viewBox="0 0 11 10" aria-hidden="true"><rect x="1" y="1" width="9" height="6"/><path d="M3.5 9.2 H7.5"/></svg>
        <span>www.briskinquiries-demo.com.au</span>
      </li>
    </ul>
    <address class="address">PO Box 58<br>Carnwell NSW 2291</address>
  </section>

  <section class="card card--back" aria-label="Business card back">
    <div class="brand">
      <span>Brisk Inquiries</span>
      <span class="brand__dot"></span>
    </div>
  </section>
</main>
</body>
</html>
```